Company brochure for our unique consulting business

We are a small consulting business offering a unique set of services to our clients.. In simple terms we are a business improvement consultancy helping our clients get the best out of their businesses. We work with clients across multiple sectors and deliver a variety of services. We want to put together a brochure to cover these main themes:1. Who we are2. What we do3. The type of people we employ4. The sectors we work inWhile the brochure needs to have a certain corporate feel to it, we don't want it to be "boring" or "stiff". We would like it to have a slightly "friendly" or "informal" feel to it, to reflect the type of organisation we are.We have a company website http://brevalconsultingpartners.net , however we do not want to directly replicate the content or feel as we recognise it needs updating.We would like the brochure to be A4 portrait format. We anticipate requiring 12 sides (including covers) but we are happy to be guided on this based on the content we have provided.The attached ppt file gives the detail of the content to be included and also shows the proposed pagination. For the front cover we would like to try 2 versions, one with the BCP logo and one with the Breval Consulting Partners logo (a file of both is attached)One of the most important pages will be the "Our Services" page. We would like this to cover the centre fold. In the ppt file we have shown an example layout, but this is where we need most help - we are clearly not graphic designers! This page will be the most used page in sales meetings etc.Also attached is the following:1. file for our BrevalConsulting Partners company logo.2. File for our BCP company logo3. Files for Derek's signatures (for under photos) - Owen's to follow4. Photo of Derek & Owen (person in purple shirt to be cropped out)Thank you and really excited to see what everyone comes back with.Derek & Owen

Target Market(s)

Very broad - Manufacturing, Healthcare, Hospitality

Industry/Entity Type

Management Consulting

Font styles to use
Other font styles liked:
• We use Swiss721, but happy to be guided by designer

Colors
3276b5
85abd2
0355a3
333333
5c5c5c
9d9d9d
d9d9d9

Requirements
Must have
• Corporate feel
Nice to have
• Slightly friendly feel
• Our standard "blue" is (CORRECTION) - R55 G96 B146 #376092 and our standard grey is R197 G178, B179 - #B3B2B2, which we would like to keep, but other colours we are happy to be guided on. Brand guidelines attached.

```html
<!DOCTYPE html>
<html lang="en">
<head>
<meta charset="utf-8">
<title>Our Services</title>
<link rel="stylesheet" href="https://fonts.googleapis.com/css2?family=Open+Sans:wght@400;600;700&family=Roboto:wght@700&display=swap">
<style>
  :root {
    --navy: #0b2a7a;
    --navy-dark: #081f5e;
    --navy-light: #163a96;
    --hub-navy: #1d3c8c;
    --hub-inner: #2a4fa8;
    --bright: #2f6fe0;
    --bright-dark: #2559c4;
    --bright-light: #3a80f0;
    --ring: #d3dadf;
    --line: #2956c8;
    --ink: #1a1a1a;
    --label-blue: #1f55c7;
    --header-a: #1f4fd0;
    --header-b: #6aa6f5;
    --bar: #3c4a55;
    --corner: #c9d2d6;
    --paper: #ffffff;
  }
  html, body { margin: 0; padding: 0; overflow: hidden; background: var(--paper); }
  .page { width: 848px; height: 1200px; position: relative; overflow: hidden; background: var(--paper); }
  .page svg { display: block; width: 848px; height: 1200px; }
  .node-label { font-family: "Open Sans", Arial, sans-serif; font-size: 14px; fill: var(--ink); text-anchor: middle; }
  .node-label.left { text-anchor: start; }
  .offer-label { font-family: "Open Sans", Arial, sans-serif; font-weight: 700; font-size: 17px; fill: var(--label-blue); }
  .hub-title { font-family: "Open Sans", Arial, sans-serif; font-weight: 700; font-size: 22px; fill: #fff; text-anchor: middle; }
  .page-title { font-family: "Roboto", Arial, sans-serif; font-weight: 700; font-size: 40px; fill: #fff; }
  .tagline { font-family: "Open Sans", Arial, sans-serif; font-size: 20px; fill: var(--ink); letter-spacing: 0.3px; }
  .page-number { font-family: "Open Sans", Arial, sans-serif; font-size: 26px; fill: var(--ink); }
  .link-solid { stroke: var(--line); stroke-width: 6; }
  .link-dot { stroke: var(--line); stroke-width: 4; stroke-dasharray: 4 4; fill: none; }
</style>
</head>
<body>
<main class="page">
<svg viewBox="0 0 1060 1500" xmlns="http://www.w3.org/2000/svg">
  <defs>
    <linearGradient id="header-grad" x1="0" x2="1" y1="0" y2="0">
      <stop offset="0" stop-color="var(--header-a)"/>
      <stop offset="1" stop-color="var(--header-b)"/>
    </linearGradient>
    <linearGradient id="band-grad" x1="0" x2="1">
      <stop offset="0" stop-color="#1d45b8"/>
      <stop offset="1" stop-color="#2f63d8"/>
    </linearGradient>
    <g id="hex-service">
      <polygon points="-62,0 -31,-54 31,-54 62,0 31,54 -31,54" fill="var(--ring)"/>
      <polygon points="-54,0 -27,-47 27,-47 54,0 27,47 -27,47" fill="var(--navy)"/>
      <polygon points="0,0 -27,-47 27,-47" fill="var(--navy-light)" opacity="0.5"/>
      <polygon points="0,0 -54,0 -27,47" fill="var(--navy-dark)" opacity="0.7"/>
    </g>
    <g id="hex-offer">
      <polygon points="-60,0 -30,-52 30,-52 60,0 30,52 -30,52" fill="var(--ring)"/>
      <polygon points="-52,0 -26,-45 26,-45 52,0 26,45 -26,45" fill="var(--bright-dark)"/>
      <polygon points="0,0 -26,-45 26,-45 52,0" fill="var(--bright-light)" opacity="0.7"/>
      <polygon points="0,0 -52,0 -26,45" fill="var(--bright-dark)"/>
    </g>
  </defs>

  <!-- header -->
  <g role="img" aria-label="Blue city skyline of tall towers">
    <rect x="0" y="0" width="1060" height="155" fill="url(#header-grad)"/>
  </g>
  <rect x="0" y="155" width="1060" height="9" fill="var(--bar)"/>
  <text class="page-title" x="712" y="130">Our Services</text>

  <!-- connectors -->
  <line class="link-solid" x1="0" y1="596" x2="405" y2="612"/>
  <line class="link-solid" x1="448" y1="690" x2="205" y2="948"/>
  <g class="link-dot">
    <line x1="503" y1="615" x2="215" y2="385"/>
    <line x1="503" y1="615" x2="400" y2="418"/>
    <line x1="503" y1="615" x2="555" y2="410"/>
    <line x1="503" y1="615" x2="720" y2="328"/>
    <line x1="503" y1="615" x2="275" y2="528"/>
    <line x1="503" y1="615" x2="678" y2="498"/>
    <line x1="503" y1="615" x2="938" y2="515"/>
    <line x1="503" y1="615" x2="143" y2="668"/>
    <line x1="503" y1="615" x2="760" y2="645"/>
    <line x1="503" y1="615" x2="265" y2="758"/>
    <line x1="503" y1="615" x2="815" y2="780"/>
    <line x1="503" y1="615" x2="490" y2="820"/>
    <line x1="503" y1="615" x2="775" y2="928"/>
    <line x1="503" y1="615" x2="638" y2="1005"/>
    <line x1="152" y1="1035" x2="353" y2="938"/>
    <line x1="152" y1="1035" x2="432" y2="1072"/>
    <line x1="152" y1="1035" x2="272" y2="1170"/>
    <line x1="152" y1="1035" x2="92" y2="1210"/>
    <line x1="0" y1="990" x2="60" y2="1005"/>
    <line x1="0" y1="1080" x2="60" y2="1062"/>
  </g>

  <!-- service nodes -->
  <use href="#hex-service" x="215" y="385"/>
  <use href="#hex-service" x="400" y="418"/>
  <use href="#hex-service" x="555" y="410"/>
  <use href="#hex-service" x="720" y="328"/>
  <use href="#hex-service" x="275" y="528"/>
  <use href="#hex-service" x="678" y="498"/>
  <use href="#hex-service" x="938" y="515"/>
  <use href="#hex-service" x="143" y="668"/>
  <use href="#hex-service" x="760" y="645"/>
  <use href="#hex-service" x="265" y="758"/>
  <use href="#hex-service" x="815" y="780"/>
  <use href="#hex-service" x="490" y="820"/>
  <use href="#hex-service" x="775" y="928"/>
  <use href="#hex-service" x="638" y="1005"/>

  <g class="node-label-set">
    <text class="node-label" x="200" y="305">LEADERSHIP COACHING</text>
    <text class="node-label" x="200" y="322">&amp; MENTORIING</text>
    <text class="node-label" x="398" y="342">PROCESS</text>
    <text class="node-label" x="398" y="359">DESIGN</text>
    <text class="node-label" x="553" y="334">FACILITY</text>
    <text class="node-label" x="553" y="351">DESIGN</text>
    <text class="node-label" x="719" y="252">NEW PRODUCT</text>
    <text class="node-label" x="719" y="269">INTRODUCTION</text>
    <text class="node-label" x="191" y="499">QUALITY</text>
    <text class="node-label" x="191" y="516">SYSTEMS</text>
    <text class="node-label" x="756" y="435">PROGRAM MANAGEMENT</text>
    <text class="node-label" x="756" y="452">&amp; PMO</text>
    <text class="node-label" x="937" y="435">LOGISTICS AND</text>
    <text class="node-label" x="937" y="452">PLANNING</text>
    <text class="node-label" x="132" y="741">EQUIPMENT</text>
    <text class="node-label" x="132" y="758">DESIGN</text>
    <text class="node-label" x="870" y="618">PERSONAL</text>
    <text class="node-label" x="870" y="635">DEVELOPMENT</text>
    <text class="node-label" x="188" y="806">BUSINESS</text>
    <text class="node-label" x="188" y="823">ASSESSMENT</text>
    <text class="node-label" x="932" y="737">SENIOR LEADERSHIP</text>
    <text class="node-label" x="932" y="754">DEVELOPMENT</text>
    <text class="node-label" x="491" y="891">SUPPLY CHAIN</text>
    <text class="node-label" x="491" y="908">DEVELOPMENT</text>
    <text class="node-label" x="882" y="943">STRATEGY</text>
    <text class="node-label" x="882" y="960">DEVELOPMENT</text>
    <text class="node-label" x="751" y="1036">ORGANIZATIONAL</text>
    <text class="node-label" x="751" y="1053">DESIGN</text>
  </g>

  <!-- business improvement hub -->
  <g class="hub hub-business">
    <polygon points="385,615 444,507 562,507 621,615 562,723 444,723" fill="var(--ring)"/>
    <polygon points="397,615 450,518 556,518 609,615 556,712 450,712" fill="var(--hub-navy)"/>
    <polygon points="420,615 462,543 544,543 586,615 544,687 462,687" fill="var(--hub-inner)"/>
    <text class="hub-title" x="503" y="600">Business</text>
    <text class="hub-title" x="503" y="627">Improvement</text>
  </g>

  <!-- organizational readiness hub -->
  <g class="hub hub-readiness">
    <polygon points="32,1035 92,931 212,931 272,1035 212,1139 92,1139" fill="var(--ring)"/>
    <polygon points="44,1035 98,942 206,942 260,1035 206,1128 98,1128" fill="var(--bright)"/>
    <polygon points="44,1035 98,942 206,942 260,1035" fill="var(--bright-light)" opacity="0.5"/>
    <text class="hub-title" x="152" y="1034">Organizational</text>
    <text class="hub-title" x="152" y="1061">Readiness</text>
  </g>

  <use href="#hex-offer" x="353" y="938"/>
  <use href="#hex-offer" x="432" y="1072"/>
  <use href="#hex-offer" x="272" y="1170"/>
  <use href="#hex-offer" x="92" y="1210"/>
  <text class="offer-label" x="406" y="971">OPTIMIZATION</text>
  <text class="offer-label" x="483" y="1109">GROWTH</text>
  <text class="offer-label" x="325" y="1207">MERGER</text>
  <text class="offer-label" x="36" y="1284">SEPARATION</text>

  <text class="tagline" x="559" y="1289">Three  blended offerings, tailored</text>
  <text class="tagline" x="559" y="1321">to your organisation.</text>

  <!-- footer -->
  <polygon points="1060,1175 1060,1500 900,1500 900,1410" fill="var(--corner)"/>
  <polygon points="0,1405 957,1405 900,1500 0,1500" fill="url(#band-grad)"/>
  <rect x="0" y="1403" width="957" height="3" fill="var(--bar)"/>
  <text class="page-number" x="987" y="1445">7</text>
  <polygon points="980,1460 1060,1460 1060,1478 970,1478" fill="var(--bar)"/>
</svg>
</main>
</body>
</html>
```